Business card design for a dynamic IT consulting company

We need a business card design for a young firm, specialized in the Telecommunications/Consulting industry. The name of the company is Quindor and Partners Business Consulting Ltd. (Short name: Quindor and Partnes)
Quindor = solve read reverse, so we aim to be uncomplicated and solution-oriented. The small pipe in our logo is also related to the word solve. So we need a new business card design, which is simple, eye catching and something non traditional (I would probably prefer a square shaped design rather than a rectangle, but open for suggestions). Attached our logo.

Target Market(s)

Usually our customers are Tier1 Telecoms providers (Q-Netra, Palorix, etc) and their executives.

Industry/Entity Type

Business

Contact Information for Business Card

Name: Bence Tolnavari
Email: b.tolnavari@quindor.hu
Web: www.quindor.hu
Mobile: +36 30 518 2769
Title: Managing Director

Optional:
Company name: Quindor and Partners Ltd.
Address: 1087 Budapest, Tolvenka str. 28/C, Hungary

Font styles to use
Other font styles liked:
• helveticaneue_medium, Prime Regular are used now.

Colors

Designer to choose colors to be used in the design.

Requirements
Must have
• I would like to have a 2 sided design.
Nice to have
• I thought if we make the logo a bit bigger (without the company name), that could go to the back with the company name below. I though, if the pipe in the logo is somehow touchable on the business card, would be nice and unique.

```html
<!DOCTYPE html>
<html lang="en">
<head>
<meta charset="utf-8">
<title>Quindor and Partners – Business Card</title>
<link href="https://fonts.googleapis.com/css2?family=Arimo:wght@400;700&display=swap" rel="stylesheet">
<style>
  :root {
    --backdrop: #594838;
    --card: #f4f4f2;
    --ink: #4a4a4a;
    --blue: #0a96d4;
    --magenta: #b0309a;
    --rule-gray: #5e6266;
  }
  html, body {
    margin: 0;
    padding: 0;
    width: 1200px;
    height: 960px;
    overflow: hidden;
    background: var(--backdrop);
    font-family: "Arimo", Helvetica, Arial, sans-serif;
  }
  .canvas {
    position: relative;
    width: 1200px;
    height: 960px;
  }
  .card {
    position: absolute;
    top: 309px;
    width: 342px;
    height: 343px;
    background: var(--card);
  }
  .card--front { left: 235px; }
  .card--back { left: 623px; }

  .frame {
    position: absolute;
    box-sizing: border-box;
  }
  .frame--outer { inset: 10px 10px 11px 10px; border: 2px solid var(--rule-gray); }
  .frame--middle { inset: 14px 14px 15px 14px; border: 2px solid var(--blue); }
  .frame--inner { inset: 18px 18px 19px 18px; border: 2px solid var(--magenta); }

  .contact {
    position: absolute;
    left: 0;
    right: 0;
    top: 88px;
    text-align: center;
    color: var(--ink);
  }
  .contact__name {
    margin: 0;
    font-size: 19px;
    font-weight: 700;
    color: var(--blue);
    line-height: 22px;
  }
  .contact__title {
    margin: 0;
    font-size: 15px;
    line-height: 20px;
    letter-spacing: 0.3px;
  }
  .contact__address {
    margin: 12px 0 0;
    font-size: 13.5px;
    line-height: 18px;
    font-style: normal;
  }
  .contact__lines {
    margin: 11px 0 0;
    font-size: 13.5px;
    line-height: 18px;
  }
  .contact__label {
    font-weight: 700;
    color: var(--blue);
  }
  .contact__web {
    position: absolute;
    left: 0;
    right: 0;
    top: 276px;
    text-align: center;
    font-size: 13px;
    letter-spacing: 7px;
    color: var(--ink);
  }

  .brand {
    position: absolute;
    left: 0;
    right: 0;
    top: 152px;
    display: flex;
    justify-content: center;
    align-items: center;
    gap: 10px;
  }
  .brand__mark {
    width: 12px;
    height: 12px;
    background: var(--magenta);
  }
  .brand__name {
    font-size: 30px;
    font-weight: 400;
    color: var(--ink);
    letter-spacing: 0.5px;
  }
</style>
</head>
<body>
<main class="canvas">
  <section class="card card--front" aria-label="Card front">
    <div class="frame frame--outer"></div>
    <div class="frame frame--middle"></div>
    <div class="frame frame--inner"></div>
    <div class="contact">
      <h1 class="contact__name">BENCE TOLNAVARI</h1>
      <p class="contact__title">MANAGING DIRECTOR</p>
      <address class="contact__address">
        Quindor and Partners Ltd.<br>
        1087 Budapest<br>
        Tolvenka str. 28/C, Hungary
      </address>
      <p class="contact__lines">
        <span class="contact__label">P:</span> +36 30 518 2769<br>
        <span class="contact__label">E:</span> b.tolnavari@quindor.hu
      </p>
    </div>
    <div class="contact__web">www.quindor.hu</div>
  </section>

  <section class="card card--back" aria-label="Card back">
    <div class="brand">
      <span class="brand__mark"></span>
      <span class="brand__name">Quindor</span>
    </div>
  </section>
</main>
</body>
</html>
```